Fern Hollow Academy business card

we need to incorporate our school logo, name, address onto a great new school business card for all our staff - I included a lot of detail below under must haves and I included 3 business card samples below also that give a flavour of what I want - I would like to include a great graphic on at least one side of the card that represents education -

Target Market(s)

this business card will need to be attractive to parents of all ages but especially millennial parents and even high school students who may influence parents to chose Fern Hollow Academy

Industry/Entity Type

Education

Contact Information for Business Card

should contain core value words "excellence service family belief"
will need out school name, Fern Hollow Academy to be present, address 7318 Marwick Avenue, Burnaby, British Columbia K3R8P1
telephone 604.781.2937 Ext. 216
first card will need my name on it, Marisol Thenkley, Director of Development & Operations
also web address of fernhollowacademy.example

Font styles to use
Other font styles liked:
• Tw Cent MT

Requirements
Must have
• a fresh modern look for a private school environment that appeals to parents looking for great education - must use school logo, and incorporate colours navy blue, CMYK 100, 60, 0, 56 and burgundy CMYK 27, 98, 81, 50
• below I uploaded 3 business card layouts that look interesting to me - I'd like to incorporate some great school photos into the design - I tried to upload some school photos that we have, that the files are too large apparently? so I could send a link to Filecrate or something like that to share great high res pics that would look nice - we are kindergarten to Gr. 12 school, so I would like to include images that would represent great education at any age.
Nice to have
• spot colour would be nice as an option for printing for maybe key administrator business cards, while the rest would be basic printing

```html
<!DOCTYPE html>
<html lang="en">
<head>
<meta charset="utf-8">
<title>Fern Hollow Academy – Business Card</title>
<link href="https://fonts.googleapis.com/css2?family=Jost:wght@400;500;700&display=swap" rel="stylesheet">
<style>
  :root{
    --navy:#002d70;
    --burgundy:#5d0318;
    --ink-white:#ffffff;
    --paper:#ffffff;
    --stage:#e6e8ec;
    --photo-dark:#1d1613;
    --photo-mid:#5a3a2c;
    --photo-red:#8e1a1f;
    --photo-skin:#b98868;
  }
  *{box-sizing:border-box;margin:0;padding:0}
  html,body{width:1200px;height:900px;overflow:hidden}
  body{
    background:var(--stage);
    font-family:"Jost",sans-serif;
    position:relative;
  }
  .card{
    position:absolute;
    left:250px;
    width:700px;height:400px;
    border-radius:22px;
    overflow:hidden;
    box-shadow:0 10px 30px rgba(0,0,0,.18);
  }
  /* front */
  .card--front{top:40px;background:var(--paper)}
  .front-mark{
    position:absolute;left:0;right:0;top:105px;
    display:flex;flex-direction:column;align-items:center;gap:14px;
  }
  .front-mark__dot{
    width:58px;height:58px;border-radius:50%;background:var(--navy);
  }
  .front-mark__name{
    font-size:30px;font-weight:500;color:var(--navy);letter-spacing:.5px;
  }
  .front-web{
    position:absolute;left:0;right:0;top:268px;text-align:center;
    font-size:17px;color:var(--navy);font-weight:500;
  }
  .front-web strong{color:var(--burgundy);font-weight:700}
  .front-values{
    position:absolute;left:0;right:0;top:300px;text-align:center;
    font-size:19px;letter-spacing:2.5px;color:var(--navy);font-weight:500;
  }
  /* back */
  .card--back{top:480px}
  .back-art{position:absolute;inset:0}
  .back-name{
    position:absolute;left:380px;top:14px;
    font-size:30px;color:var(--ink-white);font-weight:400;
  }
  .back-title{
    position:absolute;left:366px;top:56px;
    font-size:14px;color:var(--ink-white);letter-spacing:.3px;
  }
  .back-address{
    position:absolute;right:34px;top:150px;text-align:right;
    font-size:15px;line-height:1.35;color:var(--ink-white);
    text-shadow:0 1px 3px rgba(0,0,0,.6);
  }
  .back-contact{
    position:absolute;right:22px;top:282px;
    list-style:none;font-size:15px;line-height:1.45;color:var(--ink-white);
  }
  .back-contact li{display:flex;justify-content:flex-end;align-items:center;gap:8px}
  .back-contact svg{width:11px;height:11px;flex:none}
  .back-contact .web{font-weight:700}
  .back-mark{
    position:absolute;left:120px;top:250px;
    display:flex;align-items:center;gap:12px;
  }
  .back-mark__dot{width:40px;height:40px;border-radius:50%;border:2px solid var(--ink-white)}
  .back-mark__name{font-size:24px;font-weight:500;color:var(--ink-white)}
</style>
</head>
<body>

<section class="card card--front" aria-label="Card front">
  <div class="front-mark">
    <span class="front-mark__dot"></span>
    <span class="front-mark__name">Fern Hollow Academy</span>
  </div>
  <p class="front-web">www.<strong>fernhollowacademy</strong>.example</p>
  <p class="front-values">EXCELLENCE SERVICE FAMILY BELIEF</p>
</section>

<section class="card card--back" aria-label="Card back">
  <svg class="back-art" viewBox="0 0 700 400" width="700" height="400">
    <defs>
      <linearGradient id="photoTone" x1="0" y1="0" x2="1" y2="1">
        <stop offset="0" stop-color="var(--photo-mid)"/>
        <stop offset=".35" stop-color="var(--photo-skin)"/>
        <stop offset=".6" stop-color="var(--photo-red)"/>
        <stop offset="1" stop-color="var(--photo-dark)"/>
      </linearGradient>
    </defs>
    <rect width="700" height="400" fill="url(#photoTone)" role="img" aria-label="Photo of graduating students in caps and gowns"/>
    <polygon points="340,0 700,0 700,70 352,128" fill="var(--navy)"/>
    <polyline points="334,0 346,132 700,74" fill="none" stroke="#fff" stroke-width="3"/>
    <polygon points="450,400 700,400 700,215 525,252" fill="var(--navy)"/>
    <polyline points="440,400 518,246 700,208" fill="none" stroke="#fff" stroke-width="3"/>
  </svg>

  <h1 class="back-name">Marisol Thenkley</h1>
  <p class="back-title">Director of Development &amp; Operations</p>

  <p class="back-address">7318 Marwick Avenue, Burnaby<br>British Columbia K3R8P1</p>

  <ul class="back-contact">
    <li>604.781.2937 Ext. 216
      <svg viewBox="0 0 12 12"><path d="M2 1l2.5 0 1 3-1.5 1a7 7 0 0 0 3 3l1-1.5 3 1V10a1 1 0 0 1-1 1A9 9 0 0 1 1 2a1 1 0 0 1 1-1z" fill="#fff"/></svg></li>
    <li>info@fernhollowacademy.example
      <svg viewBox="0 0 12 12"><rect x="1" y="2.5" width="10" height="7" fill="none" stroke="#fff"/><path d="M1 2.5l5 4 5-4" fill="none" stroke="#fff"/></svg></li>
    <li class="web">www.fernhollowacademy.example
      <svg viewBox="0 0 12 12"><circle cx="6" cy="6" r="5" fill="none" stroke="#fff"/><path d="M1 6h10M6 1c-3 3-3 7 0 10M6 1c3 3 3 7 0 10" fill="none" stroke="#fff" stroke-width=".8"/></svg></li>
  </ul>

  <div class="back-mark">
    <span class="back-mark__dot"></span>
    <span class="back-mark__name">Fern Hollow Academy</span>
  </div>
</section>

</body>
</html>
```